Hip surgeon needs a educative book cover design

I need to re-design my old book cover for its 3rd edition.
It's a small book dedicated to my patients, who underwent total hip replacement. It's meant to help people getting around the basic care after a total hip replacement surgery and getting back to their normal, active life.
The title is: "Morning light rituals: a quiet companion".
I already had a new logo, new stationery and new website design from ArtFolio (please see the attachments).
The final design should be look alike the other fresh new designs. It must communicate health, peacefulness.
I also attached the manual as it looks today for reference.
A5 size.
Just cover and back cover.
Health

```html
<!DOCTYPE html>
<html lang="en">
<head>
<meta charset="utf-8">
<title>Morning Light Rituals – Cover</title>
<link href="https://fonts.googleapis.com/css2?family=Oswald:wght@400;600;700&family=Roboto:wght@400&display=swap" rel="stylesheet">
<style>
  :root {
    --backdrop: #e9eaec;
    --paper: #ffffff;
    --blue: #3f86cc;
    --blue-light: #6aaee6;
    --blue-dark: #2f6fb4;
    --bone-light: #e4ecf8;
    --bone-mid: #b7c9ea;
    --ink-white: #ffffff;
  }
  * { margin: 0; padding: 0; box-sizing: border-box; }
  html, body {
    width: 1200px; height: 800px; overflow: hidden;
    background: var(--backdrop);
  }
  .canvas {
    position: relative; width: 1200px; height: 800px;
  }
  .cover {
    position: absolute; left: 340px; top: 32px;
    width: 520px; height: 736px;
    background: var(--paper);
    box-shadow: 0 4px 18px rgba(0,0,0,0.12);
    overflow: hidden;
  }
  .top-band {
    position: absolute; left: 0; top: 0; width: 100%; height: 124px;
    background: linear-gradient(90deg, var(--blue) 0%, var(--blue-light) 100%);
    padding: 38px 34px 0;
  }
  .top-band p {
    font-family: "Oswald", sans-serif; font-weight: 600;
    font-size: 12.5px; line-height: 1.35; letter-spacing: 0.2px;
    color: var(--ink-white); text-align: center;
  }
  .title-block {
    position: absolute; left: 0; top: 150px; width: 100%;
    text-align: center;
    font-family: "Oswald", sans-serif; color: var(--blue);
  }
  .title-main {
    font-weight: 700; font-size: 62px; line-height: 1.02;
    text-transform: uppercase; letter-spacing: 0.5px;
  }
  .title-rule {
    width: 410px; height: 4px; margin: 12px auto 10px;
    background: var(--blue);
  }
  .title-sub {
    font-weight: 600; font-size: 40px; line-height: 1;
    text-transform: uppercase; letter-spacing: 0.5px;
  }
  .illustration {
    position: absolute; left: 70px; top: 388px;
    width: 380px; height: 240px;
    border-radius: 8px;
    background: radial-gradient(ellipse at 50% 45%, var(--bone-mid) 0%, var(--bone-light) 60%, var(--paper) 100%);
  }
  .bottom-bar {
    position: absolute; left: 0; bottom: 34px;
    width: 330px; height: 42px;
    background: linear-gradient(90deg, var(--blue-dark), var(--blue-light));
  }
  .edge-tab {
    position: absolute; right: 0; top: 610px;
    width: 18px; height: 30px; background: var(--blue);
  }
  .brand {
    position: absolute; left: 352px; bottom: 42px;
    display: flex; align-items: center; gap: 8px;
  }
  .brand-dot {
    width: 24px; height: 24px; border-radius: 50%;
    background: var(--blue);
  }
  .brand-name {
    font-family: "Oswald", sans-serif; font-weight: 400;
    font-size: 15px; color: var(--blue); white-space: nowrap;
  }
</style>
</head>
<body>
<div class="canvas">
  <section class="cover">
    <header class="top-band">
      <p>Lorem ipsum dolor sit amet, consectetur adipisicing elit, sed do eiusmod tempor incididunt ut labore et dolore magna aliqua. Ut enim ad minim veniam, quis nostrud exercitation.</p>
    </header>

    <div class="title-block">
      <h1 class="title-main">Morning Light<br>Rituals</h1>
      <div class="title-rule"></div>
      <h2 class="title-sub">A Quiet Companion</h2>
    </div>

    <div class="illustration" role="img" aria-label="Pale blue rendering of a pelvis with two hip joint implants"></div>

    <div class="bottom-bar"></div>
    <div class="edge-tab"></div>

    <div class="brand">
      <span class="brand-dot"></span>
      <span class="brand-name">Dr. Lucas M. Ferreira</span>
    </div>
  </section>
</div>
</body>
</html>
```